Business card for Eyelash extension salon in Beverly Hills,California USA

We need new business card for our salon in Beverly Hills. The salon name is 'Lashvera' . We would like to have...Business name: Lashvera Name of person: will provide later Address 4720 N.Alder Crest Ave Beverly Hills , CA 90210 Phone: will provide later (Text only) Web: www.lashverastudio.example Snapgrid icon, Circlebook icon follow us for seasonal campaign and news @lashverastudiolounge Design should look elegant, high-end, clean, simple, cohesive with my brand. Please refer my brand board. Business name color will be metallic bronzy color. Im thinking grey background or white background. Thanks

Target Market(s)

25-35. Gender neutral. People who are in Entertainment business industry.
This is High-end Eyelash extension salon in Beverly Hills

Industry/Entity Type

Beauty Salon

Contact Information for Business Card

Business name: Lashvera
Name of person: will provide later
Address 4720 N.Alder Crest Ave Beverly Hills , CA 90210
Phone: will provide later (Text only)
Web: www.lashverastudio.example
Snapgrid icon, Circlebook icon
follow us for seasonal campaign and news @lashverastudiolounge

Requirements
Must have
• Beautiful, elegant, clean and simple look but very attractive and modern
Should not have
• We don't like too clutter, too busy designs.

```html
<!DOCTYPE html>
<html lang="en">
<head>
<meta charset="utf-8">
<title>Lashvera — Business Card</title>
<link rel="stylesheet" href="https://fonts.googleapis.com/css2?family=Playfair+Display:ital,wght@0,400;0,600;1,400&family=Work+Sans:wght@400&display=swap">
<style>
  :root {
    --page-bg: #dedad5;
    --card-top: #f6f4f1;
    --card-bottom: #ebe7e2;
    --bronze: #9a6a43;
    --bronze-soft: #8a6448;
    --rule: rgba(154, 106, 67, 0.6);
    --chip: #b08461;
  }
  * { box-sizing: border-box; margin: 0; padding: 0; }
  html, body {
    width: 1047px;
    height: 1200px;
    overflow: hidden;
    background: var(--page-bg);
  }
  .canvas {
    position: relative;
    width: 1047px;
    height: 1200px;
  }
  .card {
    position: absolute;
    left: 291px;
    top: 105px;
    width: 513px;
    height: 942px;
    border-radius: 24px;
    background: linear-gradient(170deg, var(--card-top) 0%, var(--card-bottom) 100%);
    box-shadow: 0 14px 34px rgba(80, 60, 45, 0.16);
    color: var(--bronze);
    text-align: center;
  }
  .brand-name {
    position: absolute;
    left: 0;
    right: 0;
    top: 262px;
    font-family: "Playfair Display", serif;
    font-weight: 400;
    font-size: 70px;
    line-height: 1;
    letter-spacing: 1px;
    color: var(--bronze);
  }
  .brand-location {
    position: absolute;
    top: 367px;
    left: 252px;
    font-family: "Work Sans", sans-serif;
    font-size: 10px;
    letter-spacing: 1.6px;
    color: var(--bronze-soft);
  }
  .divider {
    position: absolute;
    left: 40px;
    top: 475px;
    width: 454px;
    height: 1.5px;
    background: var(--rule);
  }
  .person-name {
    position: absolute;
    left: 0;
    right: 0;
    top: 557px;
    font-family: "Playfair Display", serif;
    font-weight: 600;
    font-size: 27px;
    line-height: 36px;
    letter-spacing: 1px;
    text-transform: uppercase;
  }
  .contact-list {
    position: absolute;
    left: 0;
    right: 0;
    top: 634px;
    list-style: none;
    font-family: "Work Sans", sans-serif;
    font-size: 20px;
    line-height: 28px;
    letter-spacing: 0.8px;
    color: var(--bronze-soft);
  }
  .contact-list li { height: 53.5px; }
  .contact-list .address { font-size: 17px; letter-spacing: 0.5px; }
  .contact-label {
    font-family: "Playfair Display", serif;
    font-style: italic;
  }
  .social-row {
    position: absolute;
    left: 0;
    right: 0;
    top: 880px;
    display: flex;
    justify-content: center;
    align-items: center;
    gap: 16px;
    font-family: "Work Sans", sans-serif;
    font-size: 18px;
    line-height: 26px;
    letter-spacing: 0.3px;
    color: var(--bronze-soft);
  }
  .social-item { display: flex; align-items: center; gap: 7px; }
  .social-chip {
    width: 13px;
    height: 13px;
    border-radius: 3px;
    background: var(--chip);
  }
</style>
</head>
<body>
<main class="canvas">
  <article class="card">
    <h1 class="brand-name">Lashvera</h1>
    <p class="brand-location">BEVERLY HILLS</p>

    <div class="divider"></div>

    <h2 class="person-name">Marisol Vantree</h2>

    <ul class="contact-list">
      <li><span class="contact-label">p:</span> 800-555-0187</li>
      <li><span class="contact-label">e:</span> hello@lashverastudio.example</li>
      <li>www.lashverastudio.example</li>
      <li class="address">4720 N.Alder Crest Ave, Beverly Hills, CA 90210</li>
    </ul>

    <div class="social-row">
      <span class="social-item"><span class="social-chip"></span>Snapgrid</span>
      <span class="social-item"><span class="social-chip"></span>Circlebook</span>
      <span class="social-handle">@lashverastudiolounge</span>
    </div>
  </article>
</main>
</body>
</html>
```